Residential & commercial landscaping company

Updated business cards for commercial and landscaping company. We would like to keep out logo, but just need a more updated business card.

```html
<!DOCTYPE html>
<html lang="en">
<head>
<meta charset="utf-8">
<title>Verdant Ridge – Business Cards</title>
<link rel="stylesheet" href="https://fonts.googleapis.com/css2?family=Arimo:wght@400;700&display=swap">
<style>
  :root {
    --backdrop: #3a3a3a;
    --card-black: #000000;
    --card-white: #ffffff;
    --brand-green: #1f8a3c;
    --leaf-green: #3fae3f;
    --deep-green: #0f6b2e;
    --ink: #1a1a1a;
    --muted: #555555;
  }
  * { margin: 0; padding: 0; box-sizing: border-box; }
  html, body {
    width: 1200px;
    height: 1015px;
    overflow: hidden;
    background: var(--backdrop);
    font-family: "Arimo", Arial, sans-serif;
  }
  .sheet {
    position: relative;
    width: 1200px;
    height: 1015px;
  }
  .card {
    position: absolute;
    left: 320px;
    width: 560px;
    height: 320px;
    box-shadow: 0 14px 30px rgba(0,0,0,0.45);
  }
  .card--front {
    top: 157px;
    background: var(--card-black);
    display: flex;
    align-items: center;
    justify-content: center;
  }
  .card--back {
    top: 537px;
    background: var(--card-white);
  }
  .brand {
    display: flex;
    align-items: center;
    gap: 14px;
    font-weight: 700;
    letter-spacing: -0.5px;
  }
  .brand__dot {
    width: 1em;
    height: 1em;
    border-radius: 50%;
    background: var(--leaf-green);
    flex: none;
  }
  .card--front .brand {
    font-size: 54px;
    color: var(--card-white);
  }
  .card--back .brand {
    position: absolute;
    left: 70px;
    top: 54px;
    font-size: 32px;
    color: var(--ink);
    gap: 10px;
  }
  .person {
    position: absolute;
    left: 70px;
    top: 126px;
  }
  .person__name {
    font-size: 25px;
    font-weight: 700;
    color: var(--deep-green);
    line-height: 1.1;
  }
  .person__role {
    font-size: 15px;
    color: var(--muted);
    margin-top: 2px;
  }
  .contacts {
    position: absolute;
    left: 74px;
    top: 198px;
    list-style: none;
    font-size: 15px;
    color: var(--muted);
  }
  .contacts li {
    display: flex;
    align-items: center;
    gap: 9px;
    height: 23px;
  }
  .contacts svg {
    width: 15px;
    height: 15px;
    flex: none;
  }
  .contacts .web-name { color: var(--brand-green); }
</style>
</head>
<body>
<main class="sheet">

  <section class="card card--front" aria-label="Business card front">
    <div class="brand"><span class="brand__dot"></span>Verdant Ridge</div>
  </section>

  <section class="card card--back" aria-label="Business card back">
    <div class="brand"><span class="brand__dot"></span>Verdant Ridge</div>

    <div class="person">
      <p class="person__name">Daniel Hartwell</p>
      <p class="person__role">Jr. Project Manager</p>
    </div>

    <ul class="contacts">
      <li>
        <svg viewBox="0 0 16 16" aria-hidden="true"><path fill="#3fae3f" d="M3.5 1.5l2.4 2.6-1.3 1.7c.9 1.9 2.3 3.3 4.2 4.2l1.7-1.3 2.6 2.4-1.6 2.2C6.8 13.1 2.9 9.2 1.7 3.4z"/></svg>
        555-214-0387 ext.412
      </li>
      <li>
        <svg viewBox="0 0 16 16" aria-hidden="true"><g fill="#1f8a3c"><rect x="4" y="1.5" width="8" height="4"/><rect x="1.5" y="6" width="13" height="6" rx="1"/><rect x="4" y="10" width="8" height="4.5" fill="#fff" stroke="#1f8a3c" stroke-width="1.2"/></g></svg>
        555-730-6624
      </li>
      <li>
        <svg viewBox="0 0 16 16" aria-hidden="true"><rect x="1.5" y="3.5" width="13" height="9" fill="#1f8a3c"/><path d="M1.5 3.5L8 9l6.5-5.5" fill="none" stroke="#fff" stroke-width="1.2"/></svg>
        dan@VerdantRidgeLandscape.com
      </li>
      <li>
        <svg viewBox="0 0 16 16" aria-hidden="true"><g fill="none" stroke="#1f8a3c" stroke-width="1.4"><circle cx="8" cy="8" r="6.3"/><ellipse cx="8" cy="8" rx="2.8" ry="6.3"/><path d="M1.7 8h12.6M2.8 4.8h10.4M2.8 11.2h10.4"/></g></svg>
        <span>www.<span class="web-name">VerdantRidgeLandscape</span>.com</span>
      </li>
    </ul>
  </section>

</main>
</body>
</html>
```